Mental Health Therapy Website

I need a design for a mental health therapy website. It is a private practice. The business name is Fenwick Counseling, PLLC. My name is Martin Fenwick, LMHC, NCC, DCC. I would like some of the features/menus to be Home; Welcome/About Me, Rates and Services, Common Questions, and Contact.
If possible I would like a blog on the main page that I can update with articles I write. I would like the contact page to feature a map to my location (4189 Birchmont Ave. S, Lakewood, WA 98312).
I would like to place a small photo of me on the Welcome/About page.
I am new to this so if I am forgetting anything, please ask me!!
I will upload my logo so you can fit it and the color scheme into the design.
Thank you so very much!

```html
<!DOCTYPE html>
<html lang="en">
<head>
<meta charset="utf-8">
<title>Fenwick Counseling – Mental Health Therapy Clinic</title>
<link rel="stylesheet" href="https://fonts.googleapis.com/css2?family=Open+Sans:wght@400;600;700&display=swap">
<style>
  :root{
    --green:#6a9a2e;
    --green-dark:#4f7a1e;
    --green-light:#86b443;
    --black:#1a1a1a;
    --footer:#1e1e1e;
    --grey-bg:#f0f0f0;
    --grey-border:#cfcfcf;
    --text:#333;
    --muted:#7a7a7a;
    --blue:#5eb2d8;
    --brand-blue:#1f5c9a;
  }
  *{box-sizing:border-box;margin:0;padding:0}
  html,body{width:1200px;height:1059px;overflow:hidden;background:#fff}
  body{position:relative;font-family:"Open Sans",Arial,sans-serif;color:var(--text)}
  .abs{position:absolute}

  .brand{left:174px;top:25px;display:flex;align-items:center;gap:10px}
  .brand-mark{width:62px;height:62px;border-radius:50%;background:var(--green)}
  .brand-name{font-size:30px;font-weight:600;color:var(--brand-blue);line-height:1}

  .social-top{top:48px;left:843px;display:flex;gap:3px}
  .social-top span{width:34px;height:34px;border-radius:50%;background:#3a3a3a;border:2px solid #777;display:block}

  .nav{left:172px;top:104px;width:858px;height:50px;background:var(--black);border-bottom:5px solid var(--green)}
  .nav ul{list-style:none;display:flex;height:45px}
  .nav li{color:#fff;font-size:13px;padding:0 12px;display:flex;align-items:center;border-right:1px solid #444}
  .nav li.active{background:var(--green)}
  .search{position:absolute;left:625px;top:9px;width:223px;height:26px;display:flex}
  .search-field{flex:1;background:linear-gradient(#fff,#e6e6e6);font-style:italic;color:#666;font-size:13px;padding:3px 12px}
  .search-btn{width:40px;background:var(--green);display:flex;align-items:center;justify-content:center}

  .hero{left:172px;top:154px;width:858px;height:335px;background:
    radial-gradient(ellipse 230px 150px at 720px 120px,rgba(220,40,40,.9),transparent),
    radial-gradient(ellipse 260px 220px at 720px 200px,rgba(60,150,220,.8),transparent),
    radial-gradient(ellipse 300px 200px at 150px 100px,rgba(140,40,30,.6),transparent),
    linear-gradient(90deg,#1a1a12,#0c0c0c 60%,#142030)}
  .hero-title{left:233px;top:270px;color:#fff;font-size:36px;line-height:54px;font-weight:400;text-align:center}
  .dots{left:269px;top:454px;display:flex;gap:5px}
  .dots span{width:16px;height:16px;border-radius:50%;background:#fff}
  .dots span.on{background:var(--green-light)}

  .welcome{left:172px;top:489px;width:858px;height:106px;background:var(--grey-bg);border:1px solid var(--grey-border)}
  .welcome-photo{position:absolute;left:8px;top:8px;width:117px;height:92px;background:linear-gradient(135deg,#c9a88e,#e4d4c4)}
  .welcome h2{position:absolute;left:138px;top:11px;font-size:21px;font-weight:400;color:#222}
  .welcome p{position:absolute;left:138px;top:44px;width:616px;font-size:12px;line-height:19px;color:var(--muted);text-align:justify}

  .btn{position:absolute;background:linear-gradient(var(--green-light),var(--green-dark));color:#fff;font-size:10px;font-weight:600;display:flex;align-items:center;justify-content:center;border-radius:2px}
  .btn-dark{background:#111;border-radius:4px}

  .card{top:606px;width:190px;height:197px;border:1px solid var(--grey-border);background:linear-gradient(#fff,#d4d4d4);text-align:center}
  .card-icon{height:76px;display:flex;align-items:flex-end;justify-content:center}
  .card h3{font-size:16px;font-weight:600;color:#444;margin-top:10px}
  .card p{font-family:Arial,sans-serif;font-size:8px;line-height:12px;color:#777;width:150px;margin:6px auto 0}

  .contact{left:788px;top:600px;width:242px;height:202px;background:var(--blue);border-radius:3px}
  .contact h3{text-align:center;color:#fff;font-size:18px;font-weight:400;margin-top:8px}
  .field{position:absolute;left:14px;width:214px;height:32px;background:#fff;border:1px solid #ccc;font-family:Arial,sans-serif;font-size:11px;color:#444;padding:9px 8px}

  .section-title{left:172px;top:816px;font-size:21px;font-weight:400;color:#222}
  .arrows{left:795px;top:815px;display:flex;gap:2px}
  .arrows span{width:19px;height:19px;background:#111;display:flex;align-items:center;justify-content:center}

  .article{left:172px;top:849px;width:673px;height:106px;background:var(--grey-bg);border:1px solid var(--grey-border)}
  .article-photo{position:absolute;left:2px;top:2px;width:114px;height:100px;background:linear-gradient(135deg,#b89a86,#e8e2dc 60%,#8aa)}
  .article h3{position:absolute;left:125px;top:9px;font-size:18px;font-weight:400;color:var(--green);white-space:nowrap}
  .article p{position:absolute;left:125px;top:36px;width:540px;font-size:12px;line-height:18px;letter-spacing:-0.1px;color:#333}
  .side-photo{left:853px;top:845px;width:177px;height:107px;background:linear-gradient(135deg,#999,#d6c2a8 55%,#b7b7b7)}
  .side-photo span{position:absolute;left:9px;bottom:4px;font-size:10px;font-weight:600;color:#222}

  .footer{left:0;top:968px;width:1200px;height:91px;background:var(--footer)}
  .footer p{position:absolute;left:174px;top:34px;color:#ddd;font-size:11px}
  .social-foot{position:absolute;left:810px;top:22px;display:flex;gap:7px}
  .social-foot span{width:37px;height:37px;border-radius:50%;border:2px solid #555;display:block}
</style>
</head>
<body>
  <header>
    <div class="abs brand"><span class="brand-mark"></span><span class="brand-name">Fenwick Counseling</span></div>
    <div class="abs social-top"><span></span><span></span><span></span><span></span><span></span></div>
  </header>

  <nav class="abs nav">
    <ul>
      <li class="active">HOME</li><li>ABOUT ME</li><li>RATES AND SERVICES</li><li>COMMON QUESTIONS</li><li>CONTACT</li>
    </ul>
    <div class="search">
      <div class="search-field">search</div>
      <div class="search-btn"><svg width="16" height="16" viewBox="0 0 16 16"><circle cx="6.5" cy="6.5" r="4.5" fill="none" stroke="#fff" stroke-width="2"/><line x1="10" y1="10" x2="14.5" y2="14.5" stroke="#fff" stroke-width="2.5"/></svg></div>
    </div>
  </nav>

  <section class="abs hero" role="img" aria-label="Glowing illustration of a human head profile with a colourful brain"></section>
  <h1 class="abs hero-title">MENTAL HEALTH<br>THERAPY CLINIC</h1>
  <div class="abs dots"><span></span><span class="on"></span><span></span><span></span></div>

  <section class="abs welcome">
    <div class="welcome-photo" role="img" aria-label="Portrait photo of Martin Fenwick"></div>
    <h2>WELCOME</h2>
    <p>Painful feelings such as anxiety, anger, depression, low self-esteem, and tension are a normal part of being human and can affect anyone. Sometimes these feelings are temporary and can be eased by rest, relaxation, exercise, good nutrition, and support of trusted friends.</p>
    <div class="btn" style="left:770px;top:42px;width:75px;height:26px">READ MORE</div>
  </section>

  <article class="abs card" style="left:173px">
    <div class="card-icon"><svg width="68" height="64" viewBox="0 0 68 64"><circle cx="46" cy="16" r="9" fill="#222"/><path d="M32 60c0-18 6-28 14-28s16 10 16 28z" fill="#222"/><circle cx="26" cy="14" r="12" fill="#222"/><path d="M4 64c0-24 10-36 22-36s22 12 22 36z" fill="#222"/></svg></div>
    <h3>CONSULTATION</h3>
    <p>Moleie laceneanrit musrtasu eduscasunc odioseas gravdaus nelu ctus alorem aecenas tristique orci da nec sit amet er orem ipsum.</p>
    <div class="btn" style="left:58px;top:163px;width:74px;height:27px">READ MORE</div>
  </article>
  <article class="abs card" style="left:380px">
    <div class="card-icon"><svg width="70" height="64" viewBox="0 0 70 64"><g fill="#222"><circle cx="22" cy="44" r="14"/><circle cx="50" cy="16" r="11"/><g stroke="#222" stroke-width="7"><line x1="22" y1="24" x2="22" y2="64"/><line x1="2" y1="44" x2="42" y2="44"/><line x1="8" y1="30" x2="36" y2="58"/><line x1="36" y1="30" x2="8" y2="58"/><line x1="50" y1="1" x2="50" y2="31"/><line x1="35" y1="16" x2="65" y2="16"/><line x1="40" y1="6" x2="60" y2="26"/><line x1="60" y1="6" x2="40" y2="26"/></g></g><circle cx="22" cy="44" r="5" fill="#eee"/><circle cx="50" cy="16" r="4" fill="#eee"/></svg></div>
    <h3>OUR SERVICES</h3>
    <p>Moleie laceneanrit musrtasu eduscasunc odioseas gravdaus nelu ctus alorem aecenas tristique orci da nec sit amet er orem ipsum.</p>
    <div class="btn" style="left:58px;top:163px;width:74px;height:27px">READ MORE</div>
  </article>
  <article class="abs card" style="left:588px">
    <div class="card-icon"><svg width="64" height="60" viewBox="0 0 64 60"><rect x="2" y="4" width="58" height="50" fill="none" stroke="#222" stroke-width="5"/><rect x="10" y="14" width="42" height="8" fill="#222"/><rect x="10" y="27" width="16" height="18" fill="#222"/><rect x="30" y="27" width="22" height="4" fill="#222"/><rect x="30" y="35" width="22" height="4" fill="#222"/><rect x="30" y="42" width="22" height="4" fill="#222"/></svg></div>
    <h3>SPECIAL TIPS</h3>
    <p>Moleie laceneanrit musrtasu eduscasunc odioseas gravdaus nelu ctus alorem aecenas tristique orci da nec sit amet er orem ipsum.</p>
    <div class="btn" style="left:54px;top:163px;width:74px;height:27px">READ MORE</div>
  </article>

  <aside class="abs contact">
    <h3>CONTACT &nbsp;US</h3>
    <div class="field" style="top:38px">NAME</div>
    <div class="field" style="top:80px">PHONE</div>
    <div class="field" style="top:122px">EMAIL</div>
    <div class="btn" style="left:84px;top:169px;width:73px;height:27px;font-size:15px;font-weight:400">SENT</div>
  </aside>

  <h2 class="abs section-title">LATEST ARTICLES</h2>
  <div class="abs arrows">
    <span><svg width="9" height="12"><path d="M7 1L2 6l5 5" fill="none" stroke="#fff" stroke-width="1.5"/></svg></span>
    <span><svg width="9" height="12"><path d="M2 1l5 5-5 5" fill="none" stroke="#fff" stroke-width="1.5"/></svg></span>
  </div>

  <article class="abs article">
    <div class="article-photo" role="img" aria-label="Photo of a therapist with a client"></div>
    <h3>FLYING SISTERS FROM GISBORNE</h3>
    <p>This is probably something of a record--three sisters who are all air hostesses. They are the Hartley sisters.....Marianne, Elsie, and Rosalind, daughters of Mr and Mrs H. T. Hartley,</p>
    <div class="btn btn-dark" style="left:127px;top:74px;width:73px;height:27px">READ MORE</div>
  </article>
  <div class="abs side-photo" role="img" aria-label="Photo of a therapy session treating a lower back"><span>THERAPY CLINIC</span></div>

  <footer class="abs footer">
    <p>Copyright 2014 &nbsp;THERAPY CLINIC All Rights Rights Reserved</p>
    <div class="social-foot">
      <span style="background:#3aa7d8"></span><span style="background:#3b5a9a"></span><span style="background:#4a4a4a"></span><span style="background:#d84d8c"></span><span style="background:#f4f4f4"></span>
    </div>
  </footer>
</body>
</html>
```